Website design with eCommerce for revolutionary new product in the manufacturing industry.

We need a website designed for a precision manufacturing company based in the suburbs of Minneapolis, Minnesota called Velkrin Manufacturing. We have a revolutionary new product, the TARN LOCK, to introduce and sell through an eCommerce storefront. The website would include company information, product information, and the storefront. Green is a color that represents Velkrin Manufacturing. The final design should communicate that we exclusively offer premium products at a premium price. The design should also let the customer know they are the focus of our work.

Target Market(s)

Machinists and machine shops

Industry/Entity Type

Manufacturing and machine shops

Coding

Coded - Design and coding required

Font styles to use
Sans Serif

Colors
59FF00
82FF00
B8FF75
E3FFCB
F4FFEA

Requirements
Must have
• eCommerce storefront, Made in USA references
Nice to have
• Home page, TARN LOCK Product page, About Us, Capabilities, Contact, etc.
Should not have
• Should not be too much text and reading.

```html
<!DOCTYPE html>
<html lang="en">
<head>
<meta charset="utf-8">
<title>TARN LOCK – Product</title>
<link href="https://fonts.googleapis.com/css2?family=Audiowide&family=Poppins:wght@400;500;600;700&display=swap" rel="stylesheet">
<style>
:root{
  --green:#59ff00;
  --bg:#1f1f1f;
  --panel:#252525;
  --footer:#141414;
  --field:#262626;
  --white:#ffffff;
  --muted:#d9d9d9;
}
*{margin:0;padding:0;box-sizing:border-box}
html,body{width:1200px;height:2367px;overflow:hidden;background:var(--bg)}
body{font-family:"Poppins",sans-serif;color:var(--white)}
.page{position:relative;width:1200px;height:2367px;overflow:hidden;background:var(--bg)}
.abs{position:absolute}
.display{font-family:"Audiowide",sans-serif;text-transform:uppercase}

/* header */
.site-header{left:0;top:0;width:1200px;height:76px;background:#1b1b1b;z-index:3}
.brand{font-family:"Poppins",sans-serif;font-weight:700;font-size:25px;letter-spacing:1px;color:var(--white);white-space:nowrap}
.site-header .brand{position:absolute;left:89px;top:22px}
.main-nav{position:absolute;left:262px;top:31px;display:flex;gap:17px;font-size:12.5px;font-weight:500;text-transform:uppercase;white-space:nowrap}
.nav-contact{position:absolute;left:1095px;top:0;width:105px;height:76px;background:var(--green);color:#111;font-weight:600;font-size:13px;display:flex;align-items:center;justify-content:center}

/* hero */
.hero{left:0;top:76px;width:1200px;height:400px}
.hero-title{left:0;top:196px;width:1200px;text-align:center;font-size:66px;letter-spacing:2px;z-index:2}

/* product */
.product-frame{left:87px;top:574px;width:453px;height:446px;border-radius:26px;background:var(--panel);overflow:hidden}
.product-render{width:100%;height:100%;background:radial-gradient(ellipse 55% 60% at 52% 50%,#2f8f22 0%,#1f5c18 45%,var(--panel) 75%)}
.thumb{top:1041px;width:100px;height:100px;border-radius:6px;background:linear-gradient(150deg,#4a4a4a,#2e2e2e 60%,#3a3a3a)}
.hero-render{left:620px;top:1140px;width:480px;height:580px;background:radial-gradient(ellipse 50% 55% at 50% 50%,#2f8f22 0%,#1e5a17 45%,rgba(43,43,43,0) 78%)}
.info-title{left:622px;top:572px;font-size:37px}
.info-rule{left:624px;top:623px;width:85px;height:3px;background:var(--green)}
.bullets{list-style:none;font-size:14.6px;line-height:1.35;color:var(--muted)}
.bullets > li{position:relative;padding-left:20px;margin-bottom:16px}
.bullets > li::before{content:"";position:absolute;left:0;top:6px;width:7px;height:7px;border:2px solid var(--white);border-radius:50%}
.bullets ul{list-style:none;margin-top:6px}
.bullets ul li{position:relative;padding-left:18px;margin-bottom:6px}
.bullets ul li::before{content:"";position:absolute;left:0;top:6px;width:7px;height:7px;border:2px solid var(--green);border-radius:50%}
.info-list{left:624px;top:662px;width:495px}
.feature-list{left:88px;top:1253px;width:500px}
.feature-list > li{margin-bottom:17px}
.btn-shop{left:89px;top:1644px;width:168px;height:42px;background:var(--green);color:#111;font-weight:700;font-size:14px;border-radius:3px;display:flex;align-items:center;justify-content:center}

/* footer */
.footer{left:0;top:1815px;width:1200px;height:552px;background:var(--footer)}
.footer-brand{left:89px;top:1868px;font-size:27px}
.footer-about{left:355px;top:1862px;width:250px;font-size:14.5px;line-height:1.55}
.call-icon{left:788px;top:1873px;width:46px;height:44px;background:#161616;border-radius:3px;display:flex;align-items:center;justify-content:center}
.call-label{left:845px;top:1886px;font-size:13px;font-weight:600;color:#111}
.call-number{left:904px;top:1872px;font-size:27px;font-weight:600;color:#111}
.col-title{top:2016px;font-size:16.5px}
.link-list{list-style:none;font-size:12px;line-height:22px}
.social-list{list-style:none;font-size:12.5px}
.social-list li{display:flex;align-items:center;gap:9px;height:24px;margin-bottom:11px}
.social-list .box{width:24px;height:24px;background:#262626;border-radius:2px;display:flex;align-items:center;justify-content:center}
.social-list .box span{width:7px;height:7px;background:var(--white)}
.contact-list{list-style:none;font-size:13px;line-height:19.5px}
.contact-list li{position:relative;margin-bottom:14px}
.contact-list svg{position:absolute;left:-22px;top:2px}
.field{left:803px;width:258px;height:35px;background:var(--field);font-size:12px;color:#cfcfcf;padding:0 14px;display:flex;align-items:center}
.btn-submit{left:803px;top:2192px;width:91px;height:34px;background:var(--white);color:#111;font-weight:600;font-size:13px;display:flex;align-items:center;justify-content:center;border-radius:2px}
.rule{left:88px;top:2301px;width:1024px;height:1px;background:#2c2c2c}
.copyright{left:0;top:2326px;width:1200px;text-align:center;font-size:13px;font-weight:600}
.to-top{left:1131px;top:2281px;width:46px;height:46px;background:var(--green);display:flex;align-items:center;justify-content:center}
</style>
</head>
<body>
<div class="page">

  <header class="site-header abs">
    <div class="brand">TARN LOCK</div>
    <nav class="main-nav">
      <span>Why Velkrin Manufacturing?</span><span>What We Do</span><span>How We Make It Better</span><span>Capabilities</span><span>Gallery</span><span>About Us</span><span>Wisdom</span>
    </nav>
    <div class="nav-contact">CONTACT</div>
  </header>

  <svg class="hero abs" width="1200" height="400" viewBox="0 0 1200 400" role="img" aria-label="Close-up photo of metal machining chips and shavings">
    <defs>
      <linearGradient id="chips" x1="0" y1="0" x2="1" y2="1">
        <stop offset="0" stop-color="#4a4540"/>
        <stop offset="0.5" stop-color="#6b645c"/>
        <stop offset="1" stop-color="#3a3632"/>
      </linearGradient>
    </defs>
    <polygon points="0,0 1200,0 1200,204 0,386" fill="url(#chips)"/>
    <polygon points="0,386 1200,204 1200,255 0,390" fill="var(--green)"/>
  </svg>
  <h1 class="hero-title display abs">Product</h1>

  <svg class="abs" style="left:767px;top:1015px" width="433" height="782" viewBox="0 0 433 782">
    <polygon points="433,0 0,391 433,782" fill="#2b2b2b"/>
  </svg>

  <div class="product-frame abs">
    <div class="product-render" role="img" aria-label="Render of the green TARN LOCK stop arm with steel stop rod"></div>
  </div>
  <div class="thumb abs" style="left:139px" role="img" aria-label="Product kit in foam case, view 1"></div>
  <div class="thumb abs" style="left:253px" role="img" aria-label="Product kit in foam case, view 2"></div>
  <div class="thumb abs" style="left:367px" role="img" aria-label="Product kit in foam case, view 3"></div>

  <h2 class="info-title display abs">Product Info</h2>
  <div class="info-rule abs"></div>
  <ul class="bullets info-list abs">
    <li>Fastest and most reliable setups</li>
    <li>The locating stop rod is the highest point, so cutting clearance is no longer an issue</li>
    <li>The stop rod is top-loading
      <ul><li>No need to slide it the full length to replace it</li></ul></li>
    <li>You can use a wide range of shapes and sizes of stop rods
      <ul><li>This means the end user can easily and quickly use almost any item at hand</li><li>No need for exact shape and size rods</li></ul></li>
    <li>The clamping mechanisms do not require material deformation to function</li>
    <li>The adjustment fasteners are visible and very easy to access for quick and simple adjustments</li>
  </ul>

  <div class="hero-render abs" role="img" aria-label="Large render of the green TARN LOCK stop arm with steel stop rod"></div>

  <ul class="bullets feature-list abs">
    <li>Only two fasteners are needed to access the full range of movements</li>
    <li>The arm can be rotated and adjusted without changing the X-axis location</li>
    <li style="font-size:13px">The system can be mounted to many different vises, the machine table or fixture surface</li>
    <li>The design is modular to allow for easy customization or replacement Plenty of room for chip and coolant evacuation</li>
    <li>Inherently square to the workholding for intuitive adjustments</li>
    <li>Allows for use with very small, or very large parts, as well as oddly shaped parts Replacement parts are readily available</li>
    <li>The materials and fasteners are very common so maintenance is simple Made in USA</li>
  </ul>
  <div class="btn-shop abs">SHOP NOW</div>

  <footer class="footer abs"></footer>
  <svg class="abs" style="left:0;top:1815px" width="1200" height="124">
    <polygon points="0,0 645,0 660,35 0,35" fill="#1b1b1b"/>
    <polygon points="660,35 1200,35 1200,124 698,124" fill="var(--green)"/>
  </svg>
  <div class="brand footer-brand abs">TARN LOCK</div>
  <p class="footer-about abs">Velkrin Manufacturing has humble roots, starting as many machine</p>
  <div class="call-icon abs">
    <svg width="18" height="18" viewBox="0 0 24 24"><path d="M6.6 10.8a15 15 0 0 0 6.6 6.6l2.2-2.2c.3-.3.7-.4 1-.2 1.1.4 2.3.6 3.6.6.6 0 1 .4 1 1V20c0 .6-.4 1-1 1A17 17 0 0 1 3 4c0-.6.4-1 1-1h3.5c.6 0 1 .4 1 1 0 1.3.2 2.5.6 3.6.1.3 0 .7-.2 1z" fill="#fff"/></svg>
  </div>
  <div class="call-label abs">Call us:</div>
  <div class="call-number abs">+123 456 7890</div>

  <h3 class="col-title display abs" style="left:144px">Helpful Links</h3>
  <ul class="link-list abs" style="left:144px;top:2053px">
    <li>Why Velkrin manufacturing?</li><li>What We Do</li><li>How We Make It Better</li><li>Capabilities</li><li>Gallery</li><li>About Us</li><li>Wisdom</li><li>Contact Us</li>
  </ul>

  <h3 class="col-title display abs" style="left:375px">Information</h3>
  <ul class="social-list abs" style="left:370px;top:2062px">
    <li><span class="box"><span></span></span>Newsfeed</li>
    <li><span class="box"><span></span></span>Microblog</li>
    <li><span class="box"><span></span></span>Search</li>
    <li><span class="box"><span></span></span>Network</li>
    <li><span class="box"><span></span></span>Video</li>
  </ul>

  <h3 class="col-title display abs" style="left:561px">Contact Us</h3>
  <ul class="contact-list abs" style="left:583px;top:2063px">
    <li><svg width="14" height="12" viewBox="0 0 14 12"><rect width="14" height="11" rx="1" fill="var(--green)"/><path d="M1 1l6 5 6-5" stroke="#141414" fill="none" stroke-width="1.5"/></svg>Email:<br>info@tarnlock.com</li>
    <li><svg width="14" height="14" viewBox="0 0 24 24"><path d="M6.6 10.8a15 15 0 0 0 6.6 6.6l2.2-2.2c.3-.3.7-.4 1-.2 1.1.4 2.3.6 3.6.6.6 0 1 .4 1 1V20c0 .6-.4 1-1 1A17 17 0 0 1 3 4c0-.6.4-1 1-1h3.5c.6 0 1 .4 1 1 0 1.3.2 2.5.6 3.6.1.3 0 .7-.2 1z" fill="var(--green)"/></svg>Phone:<br>+08 123 456 7890</li>
    <li><svg width="12" height="15" viewBox="0 0 12 16"><path d="M6 0a6 6 0 0 0-6 6c0 4.5 6 10 6 10s6-5.5 6-10a6 6 0 0 0-6-6z" fill="var(--green)"/><circle cx="6" cy="6" r="2.2" fill="#141414"/></svg>Location:<br>Some address line goes<br>here city name</li>
  </ul>

  <h3 class="col-title display abs" style="left:801px">Get In Touch</h3>
  <div class="field abs" style="top:2060px">Enter Name</div>
  <div class="field abs" style="top:2100px">Enter Company</div>
  <div class="field abs" style="top:2140px">Enter Country</div>
  <div class="btn-submit abs">SUBMIT</div>

  <div class="rule abs"></div>
  <p class="copyright abs">©COPYRIGHT 2022 TARN LOCK, ALL RIGHTS RESERVED</p>
  <div class="to-top abs">
    <svg width="12" height="16" viewBox="0 0 12 16"><path d="M6 15V2M1 7l5-5 5 5" stroke="#111" stroke-width="1.5" fill="none"/></svg>
  </div>

</div>
</body>
</html>
```